MRT Property - Business Cards

Looking for a business card & general letterhead, signage etc design for our new logo.

Colours:
000a20
0056a2
00b5ef
0088ce
68cef2

Fonts:
Poppins
Karla

Please keep look and feel of new brand - example in the zip package I sent.

```html
<!DOCTYPE html>
<html lang="en">
<head>
<meta charset="utf-8">
<title>MRT Property – Business Cards</title>
<link href="https://fonts.googleapis.com/css2?family=Poppins:wght@500;600&family=Roboto:wght@400&display=swap" rel="stylesheet">
<style>
  :root {
    --navy: #000a20;
    --brand-blue: #0056a2;
    --bright-blue: #00b5ef;
    --mid-blue: #0088ce;
    --sky-blue: #68cef2;
    --ink-grey: #4a4a4a;
    --paper: #ffffff;
    --backdrop: #e9ebee;
  }
  * { margin: 0; padding: 0; box-sizing: border-box; }
  html, body { width: 1200px; height: 900px; overflow: hidden; }
  body {
    background: var(--backdrop);
    display: flex;
    align-items: center;
    justify-content: center;
    gap: 40px;
    font-family: "Poppins", sans-serif;
  }
  .card {
    width: 540px;
    height: 309px;
    position: relative;
    box-shadow: 0 6px 18px rgba(0, 10, 32, 0.18);
  }
  .card--front {
    background: var(--navy);
    display: flex;
    align-items: center;
    justify-content: center;
  }
  .wordmark {
    color: var(--brand-blue);
    font-weight: 600;
    display: flex;
    align-items: center;
    gap: 10px;
    line-height: 1;
  }
  .wordmark__dot {
    width: 14px; height: 14px; border-radius: 50%;
    background: var(--brand-blue);
  }
  .card--front .wordmark { font-size: 46px; }
  .card--front .wordmark__dot { width: 18px; height: 18px; }

  .card--back { background: var(--paper); }
  .card--back .wordmark {
    position: absolute;
    right: 34px;
    top: 42px;
    font-size: 28px;
  }
  .holder {
    position: absolute;
    left: 40px;
    bottom: 70px;
  }
  .holder__name {
    color: var(--brand-blue);
    font-weight: 600;
    font-size: 19px;
    letter-spacing: 0.3px;
    text-transform: uppercase;
  }
  .holder__role {
    color: var(--bright-blue);
    font-weight: 500;
    font-size: 14px;
    margin-top: 2px;
  }
  .contact {
    position: absolute;
    right: 34px;
    top: 132px;
    font-family: "Roboto", sans-serif;
    color: var(--ink-grey);
    font-size: 13px;
    line-height: 1.35;
    width: 210px;
  }
  .contact__address { margin-bottom: 12px; }
  .contact__list { list-style: none; }
  .contact__item { display: flex; align-items: center; gap: 8px; margin-bottom: 2px; }
  .contact__icon { width: 13px; height: 13px; flex: none; }
</style>
</head>
<body>
  <section class="card card--front" aria-label="Business card front">
    <div class="wordmark"><span class="wordmark__dot"></span>MRT Property</div>
  </section>

  <section class="card card--back" aria-label="Business card back">
    <div class="wordmark"><span class="wordmark__dot"></span>MRT Property</div>

    <div class="contact">
      <p class="contact__address">118 W Harlow St<br>Glenwood, CA 91208</p>
      <ul class="contact__list">
        <li class="contact__item">
          <svg class="contact__icon" viewBox="0 0 16 16" aria-hidden="true">
            <circle cx="8" cy="8" r="8" fill="var(--brand-blue)"/>
            <path d="M5 4.5l1.6-.5 1 2-1 .8c.4.9 1.1 1.6 2 2l.8-1 2 1-.5 1.6c-3 .2-6.1-2.9-5.9-5.9z" fill="#fff"/>
          </svg>(555) 214-3907</li>
        <li class="contact__item">
          <svg class="contact__icon" viewBox="0 0 16 16" aria-hidden="true">
            <circle cx="8" cy="8" r="8" fill="var(--brand-blue)"/>
            <rect x="4" y="5.3" width="8" height="5.6" fill="#fff"/>
            <path d="M4 5.3l4 3 4-3" fill="none" stroke="var(--brand-blue)" stroke-width="0.9"/>
          </svg>info@mrtproperty.com</li>
        <li class="contact__item">
          <svg class="contact__icon" viewBox="0 0 16 16" aria-hidden="true">
            <circle cx="8" cy="8" r="8" fill="var(--brand-blue)"/>
            <circle cx="8" cy="8" r="4" fill="none" stroke="#fff" stroke-width="1"/>
            <path d="M4 8h8M8 4c-1.8 2.4-1.8 5.6 0 8M8 4c1.8 2.4 1.8 5.6 0 8" fill="none" stroke="#fff" stroke-width="0.8"/>
          </svg>www.mrtproperty.com</li>
      </ul>
    </div>

    <div class="holder">
      <p class="holder__name">Dorian Keller</p>
      <p class="holder__role">Managing Director</p>
    </div>
  </section>
</body>
</html>
```